Road Construction Company needs business cards

We would like a new business card designed for our business.

We're a road construction company based in Qld, Australia.

Can the business card please have the following information on it.

Name: Warren Halbeck
Position: General Manager
Phone: 0472 915 348
Email: Warren.halbeck@tovrin.com.au
Address: 87 Marrow Ave, Pendlebay, QLD, 4023
Website: www.tovrin.com.au

Visually we'd like the card to be professional and simple.

Attached is our logo.

Our website is www.tovrin.com.au

Target Market(s)

Men aged 25-60

Contact Information for Business Card

As listed in project description

Font styles to use
Serif

Requirements
Must have
• Large logo on back of card

```html
<!DOCTYPE html>
<html lang="en">
<head>
<meta charset="utf-8">
<title>Tovrin Business Card</title>
<link href="https://fonts.googleapis.com/css2?family=Poppins:wght@300;400;700&display=swap" rel="stylesheet">
<style>
  :root {
    --stage: #e3e4e6;
    --card-white: #ffffff;
    --brand-blue: #1b5db0;
    --accent-blue: #2f9fdc;
    --deep-blue: #1a57aa;
    --bright-blue: #2ba4dd;
    --text-grey: #555a60;
    --panel-grey: #e7e7e9;
    --rule-blue: #9cc6e8;
  }
  * { box-sizing: border-box; margin: 0; padding: 0; }
  html, body { width: 1200px; height: 800px; overflow: hidden; }
  body {
    background: var(--stage);
    font-family: "Poppins", sans-serif;
    position: relative;
  }
  .card {
    position: absolute;
    top: 235px;
    width: 540px;
    height: 330px;
    overflow: hidden;
    box-shadow: 0 10px 30px rgba(0,0,0,0.12);
  }
  .card-back {
    left: 40px;
    background: linear-gradient(120deg, var(--bright-blue) 0%, #1a7ac4 50%, var(--deep-blue) 100%);
  }
  .card-front { left: 620px; background: var(--card-white); }
  .decor-fill {
    position: absolute;
    inset: 0;
    background: linear-gradient(135deg, rgba(231,231,233,0) 45%, var(--panel-grey) 100%);
  }
  .back-wordmark {
    position: absolute;
    left: 0; right: 0;
    top: 128px;
    text-align: center;
    font-weight: 700;
    font-size: 64px;
    letter-spacing: 4px;
    color: var(--card-white);
    line-height: 1;
  }
  .front-wordmark {
    position: absolute;
    right: 34px;
    top: 40px;
    font-weight: 700;
    font-size: 46px;
    letter-spacing: 3px;
    color: var(--brand-blue);
    line-height: 1;
  }
  .contact-block {
    position: absolute;
    left: 30px;
    top: 48px;
    color: var(--text-grey);
  }
  .person-name {
    font-size: 19px;
    font-weight: 400;
    color: var(--brand-blue);
    text-transform: uppercase;
    letter-spacing: 0.3px;
    line-height: 1.1;
  }
  .person-role {
    font-size: 14px;
    font-weight: 300;
    margin-bottom: 18px;
  }
  .contact-line {
    display: flex;
    align-items: center;
    gap: 8px;
    font-size: 13.5px;
    font-weight: 300;
    line-height: 1.75;
    white-space: nowrap;
  }
  .contact-line svg { width: 13px; height: 13px; flex: none; fill: var(--accent-blue); }
  .domain { color: var(--accent-blue); }
  .contact-rule {
    width: 280px;
    height: 1px;
    background: var(--rule-blue);
    margin: 8px 0 6px -30px;
  }
</style>
</head>
<body>

<section class="card card-back" aria-label="Card back">
  <div class="back-wordmark">TOVRIN</div>
</section>

<section class="card card-front" aria-label="Card front">
  <div class="decor-fill" role="img" aria-label="Soft grey decorative panel"></div>
  <div class="front-wordmark">TOVRIN</div>

  <div class="contact-block">
    <h1 class="person-name">Warren Halbeck</h1>
    <p class="person-role">General Manager</p>

    <p class="contact-line">
      <svg viewBox="0 0 24 24"><path d="M6.6 10.8a15.1 15.1 0 0 0 6.6 6.6l2.2-2.2a1 1 0 0 1 1-.25 11.4 11.4 0 0 0 3.6.57 1 1 0 0 1 1 1V20a1 1 0 0 1-1 1A17 17 0 0 1 3 4a1 1 0 0 1 1-1h3.5a1 1 0 0 1 1 1c0 1.25.2 2.45.57 3.57a1 1 0 0 1-.25 1z"/></svg>
      0472 915 348
    </p>
    <p class="contact-line">
      <svg viewBox="0 0 24 24"><path d="M12 2a10 10 0 1 0 0 20 10 10 0 0 0 0-20zm0 2c.9 1.2 1.6 2.6 2 4h-4c.4-1.4 1.1-2.8 2-4zM4.3 14a8 8 0 0 1 0-4h3.4a16 16 0 0 0 0 4zm.8 2h3a14 14 0 0 0 1.4 3.3A8 8 0 0 1 5.1 16zm3-8h-3a8 8 0 0 1 4.4-3.3A14 14 0 0 0 8.1 8zM12 20c-.9-1.2-1.6-2.6-2-4h4c-.4 1.4-1.1 2.8-2 4zm2.3-6H9.7a14 14 0 0 1 0-4h4.6a14 14 0 0 1 0 4zm.2 5.3a14 14 0 0 0 1.4-3.3h3a8 8 0 0 1-4.4 3.3zm1.8-5.3a16 16 0 0 0 0-4h3.4a8 8 0 0 1 0 4zm-.4-6a14 14 0 0 0-1.4-3.3A8 8 0 0 1 18.9 8z"/></svg>
      <span>www.<span class="domain">tovrin</span>.com.au</span>
    </p>
    <p class="contact-line">
      <svg viewBox="0 0 24 24"><path d="M3 5h18a1 1 0 0 1 1 1v12a1 1 0 0 1-1 1H3a1 1 0 0 1-1-1V6a1 1 0 0 1 1-1zm9 7.5L4 7.5V9l8 5 8-5V7.5z"/></svg>
      <span>Warren.halbeck@<span class="domain">tovrin</span>.com.au</span>
    </p>
    <div class="contact-rule"></div>
    <p class="contact-line">
      <svg viewBox="0 0 24 24"><path d="M12 2a7 7 0 0 0-7 7c0 5.25 7 13 7 13s7-7.75 7-13a7 7 0 0 0-7-7zm0 9.5A2.5 2.5 0 1 1 12 6.5a2.5 2.5 0 0 1 0 5z"/></svg>
      87 Marrow Ave, Pendlebay, QLD, 4023
    </p>
  </div>
</section>

</body>
</html>
```